BRIARWELL TAVERN FRIDAY MAY 3

Flyer design for bar/nightclub event. Trying to keep a general theme with their flyers (see below) but would like to add some neon or some pop to it.

TEXT:

Briarwell Bar & Tavern Presents

LANTERNTIDE NIGHTS
GRAND OPENING EVENT

PURE HOUSE MUSIC W/

MORVEX
TOMAS HALVERO
BENNAR & ACE DRIFTWAY

21+
9PM-130AM
518 M AVENUE DAVIS CA

Target Market(s)

House/dance music crowd.

Industry/Entity Type

Night Club

Font styles to use
Sans Serif

Colors
9bcb3c
fbee3d
ffffff

Requirements
Must have
• Large DJ names
Nice to have
• General theme of the attached flyers. Neon colors that stick with the theme. Anything else that looks cool will be considered

```html
<!DOCTYPE html>
<html lang="en">
<head>
<meta charset="utf-8">
<title>Briarwell Tavern – Lanterntide Nights Grand Opening</title>
<link rel="stylesheet" href="https://fonts.googleapis.com/css2?family=Orbitron:wght@700&family=Fredoka:wght@600&family=Permanent+Marker&family=Audiowide&family=Oswald:wght@700&display=swap">
<style>
  :root {
    --ink: #000000;
    --white: #ffffff;
    --yellow: #fbee3d;
    --green: #9bcb3c;
    --neon-orange: #ff7a1a;
    --ember: #c2410c;
    --peach: #ffe3cc;
  }
  * { margin: 0; padding: 0; box-sizing: border-box; }
  html, body { width: 848px; height: 1200px; overflow: hidden; background: var(--ink); }
  .flyer {
    position: relative;
    width: 848px;
    height: 1200px;
    background: var(--ink);
    overflow: hidden;
    color: var(--white);
  }
  .fire-glow {
    position: absolute;
    left: 250px; top: 360px;
    width: 520px; height: 780px;
    background:
      radial-gradient(ellipse 38% 30% at 52% 70%, rgba(255,170,60,0.85), rgba(214,80,20,0.55) 45%, transparent 75%),
      radial-gradient(ellipse 50% 45% at 50% 82%, rgba(120,40,10,0.8), transparent 75%),
      radial-gradient(ellipse 20% 40% at 48% 40%, rgba(200,70,20,0.35), transparent 80%);
  }
  .tagline {
    position: absolute;
    top: 16px; left: 18px; right: 14px;
    font-family: "Orbitron", sans-serif;
    font-weight: 700;
    font-size: 31px;
    letter-spacing: 0.64em;
    white-space: nowrap;
  }
  .venue-mark {
    position: absolute;
    left: 324px; top: 160px;
    width: 200px;
    display: flex; flex-direction: column; align-items: center; gap: 14px;
  }
  .venue-mark .badge {
    width: 54px; height: 54px;
    background: var(--green);
  }
  .venue-mark .name {
    font-family: "Fredoka", sans-serif;
    font-weight: 600;
    font-size: 22px;
    letter-spacing: 0.08em;
    color: var(--white);
    text-align: center;
    line-height: 1.1;
  }
  .presenter {
    position: absolute;
    left: 316px; top: 302px;
    font-family: "Fredoka", sans-serif;
    font-weight: 600;
    font-size: 22px;
    line-height: 1.12;
  }
  .neon-shapes { position: absolute; inset: 0; }
  .neon-shapes polygon {
    fill: none;
    stroke: #fff2e6;
    stroke-width: 4;
    stroke-linejoin: miter;
    filter: drop-shadow(0 0 4px var(--neon-orange)) drop-shadow(0 0 10px var(--neon-orange));
  }
  .series {
    position: absolute;
    left: 566px; top: 504px;
    font-family: "Fredoka", sans-serif;
    font-weight: 600;
    font-size: 34px;
    line-height: 1.2;
    color: var(--yellow);
  }
  .headline {
    position: absolute;
    left: 536px; top: 624px;
    font-family: "Permanent Marker", sans-serif;
    font-weight: 400;
    font-size: 58px;
    line-height: 0.95;
    transform: rotate(-4deg);
    transform-origin: left top;
  }
  .headline span { display: block; }
  .headline .l2 { margin-left: -8px; }
  .headline .l3 { margin-left: 24px; }
  .lineup {
    position: absolute;
    left: 0; top: 740px;
    width: 660px;
    text-align: center;
    font-family: "Audiowide", sans-serif;
    font-size: 40px;
    line-height: 58px;
    color: var(--peach);
    text-shadow: 0 0 6px var(--neon-orange), 0 0 14px var(--ember);
    list-style: none;
  }
  .happy-hour {
    position: absolute;
    left: 310px; top: 1108px;
    font-family: "Oswald", sans-serif;
    font-weight: 700;
    font-size: 30px;
    letter-spacing: 0.06em;
    color: var(--green);
    white-space: nowrap;
  }
  .address {
    position: absolute;
    left: 394px; top: 1156px;
    font-family: "Fredoka", sans-serif;
    font-weight: 600;
    font-size: 18px;
    letter-spacing: 0.03em;
  }
</style>
</head>
<body>
  <main class="flyer">
    <div class="fire-glow" role="img" aria-label="Photo of a crackling campfire with glowing logs and rising flames"></div>

    <svg class="neon-shapes" width="848" height="1200" viewBox="0 0 848 1200" aria-hidden="true">
      <polygon points="572,196 804,104 774,352"/>
      <polygon points="16,382 186,452 36,562"/>
      <polygon points="650,1010 844,956 790,1144"/>
      <polygon points="208,1064 284,1134 174,1176"/>
    </svg>

    <p class="tagline">PURE HOUSE MUSIC W/</p>

    <div class="venue-mark">
      <div class="badge"></div>
      <div class="name">BRIARWELL TAVERN</div>
    </div>

    <p class="presenter">Briarwell Bar &amp;<br>Tavern Presents</p>

    <p class="series">LANTERNTIDE<br>NIGHTS</p>

    <h1 class="headline">
      <span class="l1">GRAND</span>
      <span class="l2">OPENING</span>
      <span class="l3">EVENT</span>
    </h1>

    <ul class="lineup">
      <li>DJ</li>
      <li>MORVEX</li>
      <li>TOMAS HALVERO</li>
      <li>BENNAR &amp; ACE DRIFTWAY</li>
    </ul>

    <p class="happy-hour">21+ · HAPPY HOUR 9PM-130AM</p>
    <p class="address">518 M AVENUE DAVIS CA</p>
  </main>
</body>
</html>
```